Poster & Flyer - Golf Tournament

Poster and Flyer (2 sperapate) is required for an upcoming Torvenne Classic Golf Tournament. Although this tournament is amongst friends only (normally 40 people) we want to announce this years (13th year) tournament a bit differently.

* Poster should grab the players (brief outline)
* Flyer should have more detail and graphics
* Design flows in each Poster/Flyer.

There are several components to the Tournament that include:

1. Tournament Logo
2. Prizes (Set of golf clubs and Hotel Accommodation)
3. FairwayLogix App (Live leaderboard)
4. Timetable of events and golf
5. Venue of Golf Tournament
6. Payment terms

All information relating to components are attached.

1. Tournament Logo - Some brief background, The "Torvenne" was religious compass like symbol that basically pointed the people in the right direction when they were being faithful. We have incorporated the Logo with a golf tournament :-).

2. 1st Prize - full set of Fitted Harrier ZEN Flux Max Golf Clubs with ZEN Golf Bag (Worth $2, 200 RRP)

2nd Prize - 2 nights 5 Star Accommodation at any Brenmore Hotel in Australia includes Breakfast. (Worth $700 RRP).

Fairway Logix is a free mobile Golf app that will take the Torvenne Classic to another level.

Easy mobile live scoring, leaderboards, chat, stats & social interactions - all real time with all popular game formats.

Bring it On!

More info go to http://www.fairwaylogix.example/

* Can you incorporate some graphics from website in Poster and Flyer.

4. Timetable document attached. Make it presentable on the Flyer.

5. If we can incorporate aspects (graphics) of the golf course e.g. Golf Course Logo's, signature holes etc.

Go to:

a. Tamblin Vale Course - http://www.tamblinvale.example.au
b. Mount Orrin Golf Resort - https://www.vtma.example.au/wps/wcm/connect/vtma/Resorts/VTMA+Resorts/VTMA+Mount+Orrin+Resort/Mount+Orrin+Golf

If you go to findora images I'm sure you can find further images relating to the golf course.

6. Payment terms: Can you please express the "early bird special"

Also I will need a extra poster without the "early bird special" once the time runs out.

If you have any further questions please do not hesitate to drop me an email.

* Please note - I will end Project early if I find a design I desire.
Updates

Please add "like us on chatterbook" logo (see attached)

chatterbook link is - http://www.chatterbook.example/Torvenneclassic

```html
<!DOCTYPE html>
<html lang="en">
<head>
<meta charset="utf-8">
<title>Torvenne Classic Golf Tournament – Poster</title>
<link href="https://fonts.googleapis.com/css2?family=Raleway:wght@300;400;600;700;800&display=swap" rel="stylesheet">
<style>
  :root{
    --page-bg:#e9e9e7;
    --paper:#ffffff;
    --ink-grey:#555a5e;
    --ink-dark:#2f3336;
    --green:#2f7a2c;
    --green-dark:#1f5a1d;
    --gold:#b8913a;
    --ball-shade:#c9cccd;
    --bar-dark:#4a4d50;
    --dash:#9ea2a4;
  }
  *{margin:0;padding:0;box-sizing:border-box}
  html,body{width:1200px;height:1000px;overflow:hidden}
  body{background:var(--page-bg);font-family:"Raleway",sans-serif;color:var(--ink-grey)}
  .poster{position:absolute;left:260px;top:20px;width:680px;height:960px;overflow:hidden;background:var(--paper);box-shadow:0 6px 24px rgba(0,0,0,.18)}
  .course-photo{position:absolute;inset:0;background:linear-gradient(180deg,#8fb6e6 0%,#cfe2f5 16%,#6f9a5a 28%,#3f6f34 40%,#d7c09a 47%,#4f9a2e 54%,#2f7a22 75%,#1f5e18 100%)}
  .ball-panel{position:absolute;inset:0}
  .event-mark{position:absolute;left:430px;top:36px;width:220px;text-align:center}
  .event-mark .dot{width:46px;height:46px;border-radius:50%;background:var(--gold);margin:0 auto 12px}
  .event-mark .name{font-weight:600;font-size:23px;letter-spacing:2px;color:var(--gold);text-transform:uppercase}
  .ball{position:absolute;border-radius:50%;background:radial-gradient(circle at 60% 40%,#ffffff 0%,#f4f5f5 55%,var(--ball-shade) 100%);box-shadow:0 2px 6px rgba(0,0,0,.25);display:flex;flex-direction:column;justify-content:center;align-items:center;text-align:center;line-height:1}
  .ball .top{font-size:26px;font-weight:400;color:var(--ink-grey)}
  .ball .bottom{font-size:26px;font-weight:400;color:var(--green);margin-top:2px}
  .ball .strong{font-weight:800;color:var(--ink-grey);font-size:26px}
  .ball-year{left:-12px;top:50px;width:128px;height:128px}
  .ball-price{left:-12px;top:245px;width:128px;height:128px}
  .ball-app{left:-12px;top:458px;width:128px;height:128px}
  .ball-hotel{left:-10px;top:754px;width:128px;height:128px}
  .ball-hotel .brand{display:flex;align-items:center;gap:6px;font-size:19px;font-weight:700;color:var(--green-dark)}
  .ball-hotel .brand i{width:12px;height:12px;border-radius:50%;background:var(--green-dark);display:block}
  .prize-photo{position:absolute;left:136px;top:600px;width:146px;height:146px;border-radius:50%;background:linear-gradient(135deg,#2b2f38 0%,#3c6fb8 45%,#d9dadb 60%,#d4752a 100%);border:5px solid #fff;box-shadow:0 2px 8px rgba(0,0,0,.3)}
  .headline{position:absolute;left:150px;top:100px;text-align:center;line-height:1}
  .headline .a{font-size:22px;font-weight:800;color:var(--green)}
  .headline .b{font-size:22px;font-weight:400;color:var(--ink-grey)}
  .early-bird{position:absolute;left:172px;top:250px;width:228px}
  .early-bird h3{background:var(--bar-dark);color:#fff;font-size:15px;font-weight:700;padding:5px 10px;text-align:center;letter-spacing:.5px}
  .early-bird h3 span{font-weight:400}
  .early-bird p{font-size:9.5px;line-height:1.7;margin-top:6px;color:var(--ink-grey)}
  .early-bird p b{color:var(--ink-dark);font-weight:700}
  .app-block{position:absolute;left:170px;top:488px;text-align:center;line-height:1}
  .app-block .a{font-size:32px;font-weight:700;color:var(--ink-grey)}
  .app-block .b{font-size:32px;font-weight:700;color:var(--green)}
  .app-block .url{font-size:12px;color:var(--green);margin-top:3px}
  .prize-first{position:absolute;left:12px;top:668px;width:120px;text-align:right;line-height:1}
  .prize-first .a{font-size:17px;color:var(--green);font-weight:400}
  .prize-first .b{font-size:22px;font-weight:800;color:var(--ink-grey)}
  .prize-first .c{font-size:6.5px;color:var(--ink-grey);margin-top:2px}
  .prize-second{position:absolute;left:126px;top:800px;line-height:1}
  .prize-second .a{font-size:20px;color:var(--green)}
  .prize-second .b{font-size:20px;color:var(--green);font-weight:600}
  .prize-second .c{font-size:7px;color:var(--ink-grey);margin-top:2px;letter-spacing:.5px}
  .contact{position:absolute;left:40px;top:914px;font-size:10px;color:var(--ink-grey)}
  .contact .phone{display:flex;align-items:center;gap:8px;margin-top:6px;font-weight:700;font-size:12px;color:var(--ink-dark)}
  .contact .phone svg{display:block}
  .flow{position:absolute;inset:0;pointer-events:none}
</style>
</head>
<body>
<main class="poster">
  <div class="course-photo" role="img" aria-label="Photo of a golf course with a bunker, green and a golfer playing out of the sand under a blue sky"></div>

  <svg class="ball-panel" width="680" height="960" viewBox="0 0 680 960" aria-hidden="true">
    <defs>
      <radialGradient id="ballShade" cx="0" cy="0.5" r="1">
        <stop offset="0.75" stop-color="#ffffff"/>
        <stop offset="0.95" stop-color="#e4e6e7"/>
        <stop offset="1" stop-color="#c3c6c8"/>
      </radialGradient>
    </defs>
    <path d="M0 0 H244 A560 560 0 0 1 317 960 H0 Z" fill="url(#ballShade)"/>
  </svg>

  <div class="event-mark">
    <div class="dot"></div>
    <div class="name">The Torvenne Classic</div>
  </div>

  <svg class="flow" width="680" height="960" viewBox="0 0 680 960" aria-hidden="true">
    <defs>
      <marker id="arrow" markerWidth="8" markerHeight="8" refX="6" refY="4" orient="auto">
        <path d="M0 0 L7 4 L0 8" fill="none" stroke="#9ea2a4" stroke-width="1.3"/>
      </marker>
    </defs>
    <g fill="none" stroke="var(--dash)" stroke-width="1.6" stroke-dasharray="6 5">
      <path d="M100 180 C150 210 150 240 120 272" marker-end="url(#arrow)"/>
      <path d="M100 375 C150 410 150 440 122 480" marker-end="url(#arrow)"/>
      <path d="M96 588 C120 620 150 620 172 612" marker-end="url(#arrow)"/>
      <path d="M176 740 C150 770 130 780 114 790" marker-end="url(#arrow)"/>
    </g>
  </svg>

  <div class="ball ball-year"><span class="top">13th</span><span class="bottom">YEAR</span></div>
  <div class="headline"><div class="a">GOLF</div><div class="b">TOURNAMENT</div></div>

  <div class="ball ball-price"><span class="top">ONLY</span><span class="strong">595$</span></div>
  <section class="early-bird">
    <h3>EARLY <span>BIRD</span> PRICE</h3>
    <p><b>a)</b> Get a $60 savings when you pay the total of $530 upfront before 15th July 2013<br>
    <b>b)</b> or Pay $300 before the 30th June to secure your place. The remaining $295 to be paid before the 30th Sept.<br>
    • Due to individual cancellations we can only refund money if someone replaces your spot.</p>
  </section>

  <div class="ball ball-app"><span class="top">MOB</span><span class="strong">APP</span></div>
  <div class="app-block"><div class="a">FAIRWAY</div><div class="b">LOGIX</div><div class="url">www.fairwaylogix.example</div></div>

  <div class="prize-photo" role="img" aria-label="Photo of a golf bag with a full set of clubs"></div>
  <div class="prize-first"><div class="a">1ST PLACE</div><div class="b">FULL SET</div><div class="c">Fitted Harrier ZEN Flux Max Golf Clubs</div></div>

  <div class="ball ball-hotel"><span class="brand"><i></i>Brenmore</span></div>
  <div class="prize-second"><div class="a">2ND PLACE</div><div class="b">5* HOTEL</div><div class="c">INCLUDING BREAKFAST</div></div>

  <div class="contact">
    Contact Colin if any questions
    <div class="phone">
      <svg width="16" height="16" viewBox="0 0 16 16" aria-hidden="true"><rect width="16" height="16" rx="3" fill="var(--green)"/><path d="M5 3.5 L6.6 3.5 L7.2 6 L6.2 6.8 C6.8 8 7.8 9 9.2 9.8 L10 8.8 L12.5 9.4 L12.5 11 C12.5 11.8 11.8 12.5 11 12.4 C7.5 12 4 8.5 3.6 5 C3.5 4.2 4.2 3.5 5 3.5 Z" fill="#fff"/></svg>
      0412 555 018
    </div>
  </div>
</main>
</body>
</html>
```